Electrician Letterhead Design MVR

We need some letterhead for our bills and other papers.
Customer address is on the right side (Swiss format)
A4 format

Design should also be applicable on Cards

Target Market(s)

Private Customers, Small Business

Industry/Entity Type

Electrician

Other font styles liked:
• incised 901

Colors
00AB8E
00BBA5
67D7C9
C6EFE9
E9F9F6

```html
<!DOCTYPE html>
<html lang="en">
<head>
<meta charset="utf-8">
<title>MVR Letterhead</title>
<link href="https://fonts.googleapis.com/css2?family=Lato:wght@400;700;900&family=Montserrat:wght@400;500&family=Italianno&display=swap" rel="stylesheet">
<style>
  :root {
    --teal: #00a08a;
    --ink: #3a3a3a;
    --contact-ink: #1e1e1e;
    --paper: #f6f6f6;
    --paper-center: #ffffff;
    --backdrop: #e3e3e3;
  }
  * { margin: 0; padding: 0; box-sizing: border-box; }
  html, body {
    width: 1153px; height: 1200px; overflow: hidden;
    background: var(--backdrop);
  }
  .letterhead {
    position: absolute; left: 176px; top: 40px;
    width: 801px; height: 1120px;
    background: radial-gradient(circle at 52% 32%, var(--paper-center) 0%, var(--paper) 45%, #f0efef 100%);
    box-shadow: 0 4px 14px rgba(0,0,0,.18);
    font-family: "Lato", sans-serif;
    color: var(--ink);
  }
  .brand { position: absolute; left: 60px; top: 47px; width: 210px; }
  .brand-name {
    font-family: "Lato", sans-serif; font-weight: 900;
    font-size: 66px; line-height: 66px; color: var(--teal);
    letter-spacing: 1px;
  }
  .brand-legal {
    font-family: "Lato", sans-serif; font-weight: 900;
    font-size: 12px; margin-top: 10px; color: var(--contact-ink);
    letter-spacing: .6px; white-space: nowrap;
  }
  .contact {
    position: absolute; left: 556px; top: 50px;
    font-family: "Montserrat", sans-serif; font-size: 12.5px;
    color: var(--contact-ink);
  }
  .contact-address { line-height: 17px; margin-bottom: 8px; }
  .contact-line { display: flex; align-items: center; height: 19px; }
  .contact-line svg { width: 12px; height: 12px; margin-right: 6px; fill: var(--teal); }
  .block { position: absolute; left: 62px; font-size: 15.5px; line-height: 19px; }
  .date { top: 247px; }
  .recipient-window { position: absolute; left: 480px; top: 247px; font-size: 15.5px; line-height: 19px; }
  .recipient-company { margin-top: 16px; }
  .salutation { top: 415px; font-size: 19.5px; font-weight: 700; line-height: 24px; }
  .body-text {
    position: absolute; left: 62px; width: 678px;
    font-size: 15px; line-height: 17.2px;
    text-align: justify; text-align-last: left;
  }
  .p1 { top: 458px; } .p2 { top: 544px; } .p3 { top: 629px; } .p4 { top: 697px; }
  .closing { top: 769px; font-size: 14.5px; }
  .signature {
    position: absolute; left: 64px; top: 806px;
    font-family: "Italianno", cursive; font-size: 46px; color: #2a2a2a;
  }
</style>
</head>
<body>
<main class="letterhead">
  <header>
    <div class="brand">
      <div class="brand-name">MVR</div>
      <div class="brand-legal">Elektrotechnik Moser GmbH</div>
    </div>
    <div class="contact">
      <p class="contact-address">45-10 Linden Ave 12,<br>Ridgeview, NY 11420</p>
      <p class="contact-line"><svg viewBox="0 0 12 12" aria-hidden="true"><path d="M1 4c0-2 2-3 5-3s5 1 5 3H8.5V3h-5v1zM3 5h6l1.5 5h-9z"/></svg>555-013-2847</p>
      <p class="contact-line"><svg viewBox="0 0 12 12" aria-hidden="true"><path d="M1 2.5h10v7H1z M1.5 3l4.5 3.5L10.5 3" stroke="#fff" stroke-width=".8"/></svg>hello@mvrelectric.example</p>
      <p class="contact-line"><svg viewBox="0 0 12 12" aria-hidden="true"><circle cx="6" cy="6" r="5.2"/><path d="M3 4c1 0 2 1 1.5 2S5 8 4 9M7 2.5c1 1 2 1 2.5 2.5S8 7 7.5 8" stroke="#fff" stroke-width=".8" fill="none"/></svg>www.mvrelectric.example</p>
    </div>
  </header>

  <p class="block date">Feb-03-2022</p>
  <address class="recipient-window" style="font-style:normal">
    <p class="recipient">Mr, Paul Berger<br>President</p>
    <p class="recipient-company">Northfield Holdings<br>123 Street Name, Suite# 10<br>City, State, 120023</p>
  </address>
  <p class="block salutation">Dear Mr, Paul</p>

  <p class="body-text p1">Lorem ipsum dolor sit amet, consectetur adipisicing elit, sed do eiusmod tempor incididunt ut labore et dolore magna aliqua. Ut enim ad minim veniam, quis nostrud exercitation ullamco laboris nisi ut aliquip ex ea commodo consequat. Duis aute irure dolor in reprehenderit in voluptate velit esse cillum dolore eu fugiat nulla pariatur.</p>
  <p class="body-text p2">Lorem ipsum dolor sit amet, consectetur adipisicing elit, sed do eiusmod tempor incididunt ut labore et dolore magna aliqua. Ut enim ad minim veniam, quis nostrud exercitation ullamco laboris nisi ut aliquip ex ea commodo consequat. Duis aute irure dolor in reprehenderit in voluptate velit esse cillum dolore eu fugiat nulla pariatur.</p>
  <p class="body-text p3">Lorem ipsum dolor sit amet, consectetur adipisicing elit, sed do eiusmod tempor incididunt ut labore et dolore magna aliqua. Ut enim ad minim veniam, quis nostrud exercitation ullamco laboris nisi ut aliquip ex ea commodo consequat.</p>
  <p class="body-text p4">Excepteur sint occaecat cupidatat non proident, sunt in culpa qui officia deserunt mollit anim id est laborum. re et dolore magnam aliquam quaerat voluptatem.</p>

  <p class="block closing">Regards</p>
  <p class="signature">Daniel Hartmann</p>
</main>
</body>
</html>
```